New Business Card Design Project

I need a design for business cards, i am an electrical business called "Corvane Electrical and Communications" i need the cards to be double sided with the company logo on the back (attached) the front needs to say my company name, web site, email address, telephone number, and ABN number and electrical license number. I am open to different arrangements of the information but would like the background to be incorporating something electrical or something that looks smart. open to all additional ideas also.

The company colours are orange and grey see logo attached.

Business Name: Corvane Electrical and Communications
Website: corvaneelectricalandcomms.example.com.au
Email: brent@corvaneelectricalandcomms.example.com.au
Telephone(mobile): 0481209736
ABN: 71208349162
Lic No: 418273D

Target Market(s)

Business entities, Project Managers, Accounts, Clients

Industry/Entity Type

Electrician

Contact Information for Business Card

I need a design for business cards, i am an electrical business called "Corvane Electrical and Communications" i need the cards to be double sided with the company logo on the back (attached) the front needs to say my company name

Font styles to use
Serif
Sans Serif

Colors
f37122
5c5c5c

Requirements
Must have
• Must have the Logo on the back open to different ways of it being on the back but had in mind to keep it central but again open to other options
Nice to have
• A real modern cool background that is eye catching yet contemporary
Should not have
• No backgrounds of a light bulb or plug or anything like that

```html
<!DOCTYPE html>
<html lang="en">
<head>
<meta charset="utf-8">
<title>Corvane Electrical and Communications – Business Card</title>
<link rel="stylesheet" href="https://fonts.googleapis.com/css2?family=Ubuntu:wght@400;500&display=swap">
<style>
  :root {
    --orange: #f37122;
    --orange-light: #f8a352;
    --orange-deep: #d85f14;
    --grey: #5c5c5c;
    --charcoal: #2b2b2d;
    --ink-light: #ececec;
    --ink-soft: #d9d9d9;
    --stage: #d8d6d3;
  }
  * { margin: 0; padding: 0; box-sizing: border-box; }
  html, body {
    width: 1200px;
    height: 969px;
    overflow: hidden;
    background: var(--stage);
    font-family: "Ubuntu", sans-serif;
  }
  .canvas {
    position: relative;
    width: 1200px;
    height: 969px;
  }
  .business-card {
    position: absolute;
    left: 365px;
    top: 80px;
    width: 470px;
    height: 820px;
    overflow: hidden;
    background: linear-gradient(160deg, var(--orange-light) 0%, var(--orange) 25%, var(--orange) 75%, var(--orange-deep) 100%);
    box-shadow: 0 10px 30px rgba(0, 0, 0, 0.25);
  }
  .signal-artwork {
    position: absolute;
    left: 0;
    top: 130px;
    width: 100%;
    height: 580px;
    background: linear-gradient(180deg,
      rgba(43, 43, 45, 0) 0%,
      var(--charcoal) 24%,
      var(--charcoal) 76%,
      rgba(43, 43, 45, 0) 100%);
  }
  .card-holder {
    position: absolute;
    top: 40px;
    width: 100%;
    text-align: center;
    color: var(--ink-light);
  }
  .holder-name {
    font-size: 27px;
    font-weight: 500;
    letter-spacing: 1px;
  }
  .holder-title {
    margin-top: 2px;
    font-size: 20px;
    letter-spacing: 1px;
    color: var(--ink-soft);
  }
  .brand {
    position: absolute;
    top: 365px;
    width: 100%;
    text-align: center;
    color: var(--ink-light);
    font-weight: 500;
  }
  .brand-name {
    font-size: 62px;
    letter-spacing: 6px;
    line-height: 1;
  }
  .brand-tagline {
    margin-top: 10px;
    font-size: 13.5px;
    letter-spacing: 1.6px;
  }
  .registration {
    position: absolute;
    top: 480px;
    width: 100%;
    text-align: center;
    font-size: 19px;
    color: var(--ink-soft);
    letter-spacing: 0.3px;
  }
  .contact-list {
    position: absolute;
    top: 714px;
    width: 100%;
    list-style: none;
    text-align: center;
    color: var(--ink-light);
  }
  .contact-item {
    display: flex;
    align-items: center;
    justify-content: center;
    gap: 6px;
    height: 31px;
    font-size: 15px;
  }
  .contact-item.phone { font-size: 21px; }
  .contact-icon {
    width: 16px;
    height: 16px;
    flex: none;
  }
</style>
</head>
<body>
<main class="canvas">
  <article class="business-card">
    <div class="signal-artwork" role="img" aria-label="Decorative orange and charcoal waveform artwork"></div>

    <header class="card-holder">
      <p class="holder-name">MARLA QUINT</p>
      <p class="holder-title">PRESIDENT</p>
    </header>

    <div class="brand">
      <p class="brand-name">CORVANE</p>
      <p class="brand-tagline">ELECTRICAL &amp; COMMUNICATIONS</p>
    </div>

    <p class="registration">ABN: 71208349162 | Lic No: 418273D</p>

    <ul class="contact-list">
      <li class="contact-item phone">
        <svg class="contact-icon" viewBox="0 0 16 16" aria-hidden="true">
          <rect x="4" y="1" width="8" height="14" rx="1.5" fill="none" stroke="currentColor" stroke-width="1.4"/>
          <circle cx="8" cy="12.5" r="0.9" fill="currentColor"/>
        </svg>
        0481209736
      </li>
      <li class="contact-item email">
        <svg class="contact-icon" viewBox="0 0 16 16" aria-hidden="true">
          <rect x="1.5" y="3.5" width="13" height="9" fill="currentColor"/>
          <path d="M1.5,3.5 L8,9 L14.5,3.5" fill="none" stroke="var(--orange)" stroke-width="1"/>
        </svg>
        brent@corvaneelectricalandcomms.example.com.au
      </li>
      <li class="contact-item website">
        <svg class="contact-icon" viewBox="0 0 16 16" aria-hidden="true">
          <circle cx="8" cy="8" r="6.3" fill="none" stroke="currentColor" stroke-width="1.4"/>
          <ellipse cx="8" cy="8" rx="2.6" ry="6.3" fill="none" stroke="currentColor" stroke-width="1"/>
          <line x1="1.7" y1="8" x2="14.3" y2="8" stroke="currentColor" stroke-width="1"/>
        </svg>
        corvaneelectricalandcomms.example.com.au
      </li>
    </ul>
  </article>
</main>
</body>
</html>
```